Systems and Technology Consultants - Website

Design & Build a website for a new company which operates in the Systems and Technology space for Transportation, Government and Commercial sectors.

Overall design should be minimalist in nature.
Should also have a feed that provides news and event updates on the main page.
Logo has already been awarded and should be incorporated into the site.

We like the overall layout, functionality and simplicity of the below sites. Submitted designs could be similar to or a combination of the aspects on these sites, or perhaps a whole different concept - we are open to new ideas.
Norvique.com
Teblo.it

Update 1 Dated 27 May 2014

All I am moving away from the Teblo.it website and would like it to be more aligned with Norvique.com not only in layout but in functionality. I will be extending the deadline of this design brief for two weeks to incorporate additional requirements and will add addtional funding to the project.

Apologies for not having more information available to provide but with so many submissions its getting confusing.

Thanks Derek

Please note that the brief has been updated and the deadline has been extended.

Important: We will need two language versions of the website, English and Arabic; the website is hosted on HostPelican

Hello All, Thank you for your submissions. We have narrowed it down to the final 6 designers and I just wanted to take a moment and provide a bit of feedback regarding the concepts that we like and the modifications we are looking for. First, let me mention some of the design functions we like. - At the top of the homepage we really like the "region" or "language" tab so that the website can be viewed in both English and Arabic. - We like the homepage to have clear color variation so that the different sections of the homepage are distinct. Additionally, we like the bottom portion of the homepage to be in red. We feel that draws attention to our contact information. Again, we would like the colors to integrate black, gray-scale, red, etc. - Having a search tab at the top of the home page, or integrated into the main image, so that the site is easy to navigate. - We especially like the main image to have the scrolling tabs at the bottom so it is easy to browse the services offered (Consultancy, Solutions Architecture, Masters Systems Integration, Independent Design Review). - In regards to the services offered tab we really like the idea that a few people presented that have the outside of our logo with an icon in the middle of consultancy, solutions, etc., etc. Secondly, as mentioned in our brief we really enjoy the design of norvique site. Specially, we enjoy the strong iconic images they use, the way the tabs at the top scroll easily, and contact us page that generates an email. Lastly, I've included some photos of the concept we have been working on. What we are trying to demonstrate is how our company offers a range of services that are essentially linked together. We provide individual services that when combined present the full service package. We would like this concept to be integrated into the over concept of our website. Please feel free to ask for clarification of any of the above points or contact us if you have any additional questions. We appreciate all of your hard work and are very excited to see the updated designs. Best, Marta Vennick Quelbrant Senior Program Manager marta.vennick@quelbrant-example.com

Industry/Entity Type

Government

Font styles to use
Serif
Sans Serif

Requirements
Must have
• Must work on/adapt to various/mobile devices (responsive)
Must be simple and straightforward
Colors should be in line/matching with logo
2 language versions: English and Arabic (no Thai)
Services should be the first group/row of items after/below the main image
Note: the website will be hosted by hostpelican
Nice to have
• Submit feedback form
What's New section
The banner at the bottom of the site should not be too large; we would like a narrow one more
It would be nice if the header/top banner (with Home, About, etc. tabs) could stay in place as you scroll down (like Norvique and Chatterloop)
We will likely only use one image with a Company slogan on the Home page rather than a carousel of images to rotate through
Should not have
• This is the existing website: http://www.quelbrant-example.org
We do not like the animation, the way the banner icons/titles bounce
Not simple enough, we don't like the functionality or how pages load so slowly
We do not like the logo centered - it should be at the left
The banner and its tabs should not be towards the right, we would like them to be centered, to go all the way across and to be below the logo

```html
<!DOCTYPE html>
<html lang="en">
<head>
<meta charset="utf-8">
<title>Quelbrant International – Integrated Systems</title>
<link rel="stylesheet" href="https://fonts.googleapis.com/css2?family=Montserrat:wght@400;500;600;700&family=Open+Sans:wght@300;400;600&family=Lato:wght@300;400;700&display=swap">
<style>
:root{
  --red:#d9252b;
  --red-dark:#c82026;
  --ink:#1c2a33;
  --text:#222;
  --muted:#666;
  --grey-bg:#f0f0f0;
  --tab-bg:#e6e6e6;
  --line:#dcdcdc;
  --footer-bar:#141414;
  --white:#fff;
}
*{margin:0;padding:0;box-sizing:border-box}
html,body{width:994px;height:1200px;overflow:hidden;background:var(--white)}
body{position:relative;font-family:"Lato",sans-serif;color:var(--text)}
.abs{position:absolute}
a{color:inherit;text-decoration:none}
h1,h2,h3,h4{font-weight:400}

/* header */
.brand{left:89px;top:36px;display:flex;align-items:center;gap:12px}
.brand-dot{width:24px;height:24px;border-radius:50%;background:var(--red);flex:none}
.brand-name{font-family:"Montserrat",sans-serif;font-weight:700;color:var(--red);font-size:22px;letter-spacing:5px;line-height:1}
.brand-sub{font-family:"Montserrat",sans-serif;font-weight:700;color:var(--red);font-size:8.5px;letter-spacing:3.4px;margin-top:5px}
.search{left:529px;top:25px;width:233px;height:29px;border:1px solid #ccc;font-size:9.5px;color:#555;padding:9px 0 0 20px;font-family:"Open Sans",sans-serif}
.search-icon{left:771px;top:31px}
.lang{left:802px;top:30px;display:flex;align-items:center;gap:7px;font-family:"Open Sans",sans-serif;font-size:13.5px;color:#555}
.lang-globe{width:30px;height:14px;border-radius:7px;background:var(--red)}
.lang-caret{margin-left:10px;width:0;height:0;border-left:5px solid transparent;border-right:5px solid transparent;border-top:8px solid var(--red)}
.nav{right:92px;top:78px;display:flex;gap:23px;font-family:"Montserrat",sans-serif;font-size:11.5px;font-weight:500;color:#111}
.nav .active{color:var(--red)}
.header-rule{left:0;top:112px;width:994px;height:4px;background:var(--red)}

/* hero */
.hero{left:0;top:116px;width:994px;height:369px;background:linear-gradient(90deg,#12303b 0%,#173c48 45%,#2d5665 70%,#1c4250 100%)}
.hero-photo{position:absolute;left:440px;top:0;width:554px;height:369px;background:radial-gradient(ellipse at 55% 45%,#9bb4bd 0%,#4d7280 40%,rgba(28,66,80,0) 75%)}
.hero-title{position:absolute;left:89px;top:108px;font-family:"Montserrat",sans-serif;font-weight:600;font-size:33px;letter-spacing:2px;color:var(--white);line-height:44px}
.hero-title .hl{color:var(--red)}
.hero-lede{position:absolute;left:94px;top:196px;font-family:"Open Sans",sans-serif;font-weight:300;font-size:20px;line-height:24px;color:var(--white)}
.hero-lede b{color:var(--red);font-weight:600}
.hero-btn{position:absolute;left:92px;top:265px;width:155px;height:32px;background:var(--red);border-radius:3px;color:var(--white);font-family:"Montserrat",sans-serif;font-weight:700;font-size:10.5px;letter-spacing:2px;display:flex;align-items:center;padding-left:19px;gap:14px;white-space:nowrap}
.dots{position:absolute;left:488px;top:337px;display:flex;gap:9px;align-items:center}
.dots span{width:9px;height:9px;border-radius:50%;background:var(--white)}
.dots .on{width:14px;height:14px;background:var(--red)}

/* services */
.svc-box{left:91px;top:516px;width:207px;height:201px;background:var(--grey-bg)}
.svc-title{position:absolute;left:12px;top:8px;width:184px;text-align:center;font-family:"Montserrat",sans-serif;font-weight:400;font-size:20px;letter-spacing:1px;color:var(--red);padding-bottom:6px;border-bottom:2px solid var(--red)}
.svc-list{position:absolute;left:14px;top:60px;list-style:none}
.svc-list li{display:flex;align-items:center;gap:13px;height:45px;font-size:14px;color:#111}
.svc-list li svg{width:34px;height:34px}

.tabs{left:312px;top:516px;width:592px;height:40px;border-bottom:1px solid var(--line);display:flex;gap:5px}
.tab{width:179px;height:40px;background:var(--tab-bg);border:1px solid #d6d6d6;display:flex;align-items:center;justify-content:center;font-size:13.5px;color:#111}
.tab.current{background:var(--white);border-bottom-color:var(--white);width:174px}
.tab-panel{left:312px;top:563px;width:592px;height:154px;background:linear-gradient(180deg,#fafafa,#f0f0f0)}
.tab-art{position:absolute;left:18px;top:24px;width:130px;height:90px;border-radius:45px 45px 18px 18px;background:linear-gradient(180deg,#9a9a9a,#7a7a7a)}
.tab-heading{position:absolute;left:165px;top:20px;font-family:"Montserrat",sans-serif;font-weight:400;font-size:23px;letter-spacing:1px;color:var(--red)}
.tab-copy{position:absolute;left:167px;top:53px;width:410px;font-family:"Lato",sans-serif;font-size:11.6px;line-height:19px;color:#222}

/* news */
.col-title{font-family:"Montserrat",sans-serif;font-weight:600;font-size:23px;letter-spacing:1.5px;color:var(--ink)}
.news{left:93px;top:745px;width:430px}
.news .col-title{padding-left:2px;height:45px;border-bottom:1px solid var(--line)}
.news-head{margin-top:14px;font-family:"Montserrat",sans-serif;font-weight:400;font-size:17.5px;color:var(--red-dark);letter-spacing:.4px;white-space:nowrap}
.news-date{margin-top:4px;font-family:"Open Sans",sans-serif;font-size:9.5px;color:#444}
.news-body{margin-top:13px;width:440px;font-family:"Open Sans",sans-serif;font-weight:300;font-size:12.3px;line-height:17px;color:#555}
.more{font-family:"Open Sans",sans-serif;font-weight:300;font-size:11px;color:#e0452a}
.news .more{display:block;margin-top:14px}
.works{left:568px;top:745px;width:322px}
.works .col-title{padding-left:11px;height:45px;border-bottom:1px solid var(--line);width:314px}
.works ul{list-style:none;margin-top:19px;padding-bottom:12px;border-bottom:1px solid var(--line)}
.works li{position:relative;padding-left:21px;margin-bottom:6px;font-family:"Open Sans",sans-serif;font-weight:300;font-size:12.3px;line-height:14px;color:#555}
.works li::before{content:"→";position:absolute;left:0;top:0;font-size:10px;color:#444}
.works .more{display:block;margin-top:20px}

/* footer */
.footer{left:0;top:971px;width:994px;height:188px;background:var(--red);color:var(--white)}
.f-brand{position:absolute;left:91px;top:34px;display:flex;align-items:center;gap:12px}
.f-brand .brand-dot{background:var(--white)}
.f-brand .brand-name,.f-brand .brand-sub{color:var(--white)}
.f-about{position:absolute;left:96px;top:95px;width:245px;font-family:"Open Sans",sans-serif;font-size:11px;line-height:16.5px}
.f-head{position:absolute;font-family:"Open Sans",sans-serif;font-weight:600;font-size:12.5px;letter-spacing:.2px}
.f-links{position:absolute;left:362px;top:61px;list-style:none;font-family:"Montserrat",sans-serif;font-size:8.5px;font-weight:500;line-height:16.6px}
.f-events{position:absolute;left:490px;top:65px;list-style:none;font-family:"Open Sans",sans-serif;font-size:10.8px}
.f-events li{display:flex;align-items:center;gap:9px;height:22.4px}
.f-contact{position:absolute;left:715px;top:59px;list-style:none;font-family:"Lato",sans-serif;font-size:10.8px;font-weight:700}
.f-contact li{display:flex;align-items:center;height:26px}
.f-contact li .ic{width:25px;display:flex}
.bottom-bar{left:0;top:1159px;width:994px;height:41px;background:var(--footer-bar);color:#ddd}
.copy{position:absolute;left:89px;top:13px;font-family:"Open Sans",sans-serif;font-size:11px}
.follow{position:absolute;left:763px;top:11px;display:flex;align-items:center;gap:7px;font-family:"Open Sans",sans-serif;font-size:13px}
.follow span.c{width:20px;height:20px;border-radius:50%;background:#4a4a4a;display:inline-block}
.follow .label{margin-right:9px}
</style>
</head>
<body>

<header>
  <div class="abs brand">
    <span class="brand-dot"></span>
    <div><div class="brand-name">QUELBRANT</div><div class="brand-sub">INTERNATIONAL</div></div>
  </div>
  <div class="abs search">Search Here ..........</div>
  <svg class="abs search-icon" width="15" height="15" viewBox="0 0 15 15"><circle cx="6" cy="6" r="4.5" fill="none" stroke="#aaa" stroke-width="2"/><line x1="9.5" y1="9.5" x2="13.5" y2="13.5" stroke="#aaa" stroke-width="2"/></svg>
  <div class="abs lang"><span class="lang-globe" role="img" aria-label="World map icon"></span>English<span class="lang-caret"></span></div>
  <nav class="abs nav">
    <a class="active">HOME</a><a>ABOUT US</a><a>BUSINESS UNITS</a><a>SERVICES</a><a>LOCATIONS</a><a>CONTACT US</a>
  </nav>
  <div class="abs header-rule"></div>
</header>

<section class="abs hero">
  <div class="hero-photo" role="img" aria-label="Photo of a man in a white shirt touching a glowing network world map"></div>
  <h1 class="hero-title">INTEGRATED <span class="hl">SYSTEMS</span><br>RELIABLE SOLUTIONS</h1>
  <p class="hero-lede"><b>QUELBRANT</b> Specializes in delivering quality<br>fessional Services and Technical Projects that</p>
  <a class="hero-btn">LEARN MORE
    <svg width="24" height="12" viewBox="0 0 24 12"><path d="M1 1l7 5-7 5M10 1l7 5-7 5" fill="none" stroke="#fff" stroke-width="1.5"/></svg>
  </a>
  <div class="dots"><span></span><span></span><span class="on"></span></div>
</section>

<aside class="abs svc-box">
  <h2 class="svc-title">Services</h2>
  <ul class="svc-list">
    <li><svg viewBox="0 0 34 34"><circle cx="17" cy="17" r="11" fill="none" stroke="#d9252b" stroke-width="5" stroke-dasharray="4 3"/><circle cx="17" cy="17" r="5" fill="#d9252b"/></svg>Consultancy</li>
    <li><svg viewBox="0 0 34 34" fill="none" stroke="#d9252b" stroke-width="1.6"><rect x="2" y="12" width="6" height="6"/><rect x="11" y="12" width="6" height="6"/><rect x="2" y="22" width="6" height="6"/><rect x="11" y="22" width="6" height="6"/><rect x="20" y="22" width="6" height="6"/><rect x="20" y="12" width="6" height="6"/><rect x="22" y="3" width="6" height="6" transform="rotate(20 25 6)"/></svg>Solutions Architecure</li>
    <li><svg viewBox="0 0 34 34"><circle cx="17" cy="17" r="11" fill="none" stroke="#d9252b" stroke-width="5" stroke-dasharray="4 3"/><circle cx="17" cy="17" r="5" fill="#d9252b"/></svg>Master Systems</li>
  </ul>
</aside>

<div class="abs tabs">
  <div class="tab current">Consultancy</div>
  <div class="tab">Solutions Architecure</div>
  <div class="tab">Master Systems</div>
</div>
<section class="abs tab-panel">
  <div class="tab-art" role="img" aria-label="Grey cloud illustration with a group of business people"></div>
  <h3 class="tab-heading">Sitquetamet dolor Ipsum amet</h3>
  <p class="tab-copy">quelbrant specializes in delivering quality professional services and technical projects that support larger business goals.&nbsp; systems are tools that support a greater business function and need. we understand that most t echnical projects are conceptualized to support a larger vision with actual</p>
</section>

<section class="abs news">
  <h2 class="col-title">Latest News</h2>
  <h3 class="news-head">Coraz mniej serwerów, coraz więcej chmury</h3>
  <div class="news-date">31 stycznia 2014</div>
  <p class="news-body">Według KDR, szefowie IT coraz szybciej przesiadają się do chmury obliczeniow między 25-30% wszystkich sprzedanych serwerów trafi nie do korporacyjnych..</p>
  <a class="more">Czytaj więcej →</a>
</section>

<section class="abs works">
  <h2 class="col-title">Featured Works</h2>
  <ul>
    <li>Nasi eksperci publikują na RackBlogu: Norlex Frame System – integracja z Vantora Sphere</li>
    <li>UE: 2,5 mln nowych miejsc pracy dzięki chmurze?</li>
    <li>E-seminarium: Zwiększania efektywności biznesu poprzez zastosowanie chmury obliczeniowej</li>
  </ul>
  <a class="more">Wszystkie aktualności →</a>
</section>

<footer class="abs footer">
  <div class="f-brand">
    <span class="brand-dot"></span>
    <div><div class="brand-name">QUELBRANT</div><div class="brand-sub">INTERNATIONAL</div></div>
  </div>
  <p class="f-about">Lorem ipsum dolorSit amet consecteturAdipsic-ing elit,ed do euismodTempor incidunt Labore et dolorMagna aliqua.Lorem ipsum dolorSit amet consecteturAdipsicing elit,</p>

  <h4 class="f-head" style="left:354px;top:41px">SITE MAP</h4>
  <ul class="f-links"><li>HOME</li><li>ABOUT US</li><li>BUSINESS UNITS</li><li>SERVICES</li><li>LOCATIONS</li><li>CONTACT US</li></ul>

  <h4 class="f-head" style="left:488px;top:41px">UP COMING EVENTS</h4>
  <ul class="f-events">
    <li><svg width="13" height="13" viewBox="0 0 13 13"><circle cx="6.5" cy="6.5" r="5" fill="none" stroke="#fff" stroke-width="1.5"/><path d="M6.5 3.5v3l2 1.5" fill="none" stroke="#fff" stroke-width="1.3"/></svg>Monday 07:00 AM — 07:00 PM</li>
    <li><svg width="13" height="13" viewBox="0 0 13 13"><circle cx="6.5" cy="6.5" r="5" fill="none" stroke="#fff" stroke-width="1.5"/><path d="M6.5 3.5v3l2 1.5" fill="none" stroke="#fff" stroke-width="1.3"/></svg>Tuesday 07:00 AM — 07:00 PM</li>
    <li><svg width="13" height="13" viewBox="0 0 13 13"><circle cx="6.5" cy="6.5" r="5" fill="none" stroke="#fff" stroke-width="1.5"/><path d="M6.5 3.5v3l2 1.5" fill="none" stroke="#fff" stroke-width="1.3"/></svg>Wednesday 07:00 AM — 07:00 PM</li>
    <li><svg width="13" height="13" viewBox="0 0 13 13"><circle cx="6.5" cy="6.5" r="5" fill="none" stroke="#fff" stroke-width="1.5"/><path d="M6.5 3.5v3l2 1.5" fill="none" stroke="#fff" stroke-width="1.3"/></svg>Thursday 07:00 AM — 07:00 PM</li>
  </ul>

  <h4 class="f-head" style="left:715px;top:36px">OUR CONTACT INFORMATION</h4>
  <ul class="f-contact">
    <li><span class="ic"><svg width="11" height="14" viewBox="0 0 11 14"><path d="M5.5 0A5 5 0 0 0 .5 5c0 4 5 9 5 9s5-5 5-9a5 5 0 0 0-5-5z" fill="#fff"/><circle cx="5.5" cy="5" r="1.8" fill="#d9252b"/></svg></span>Quelbrant International</li>
    <li><span class="ic"></span>48, Larkmoor Ave Brenfield</li>
    <li><span class="ic"><svg width="9" height="14" viewBox="0 0 9 14"><rect x=".8" y=".8" width="7.4" height="12.4" rx="1" fill="none" stroke="#fff" stroke-width="1.6"/><rect x="3" y="10.5" width="3" height="1" fill="#fff"/></svg></span>(555) 014 27 90</li>
    <li><span class="ic" style="width:29px"><svg width="15" height="11" viewBox="0 0 15 11"><rect width="15" height="11" fill="#fff"/><path d="M0 0l7.5 6L15 0" fill="none" stroke="#d9252b" stroke-width="1.2"/></svg></span>info@quelbrant-example.com</li>
  </ul>
</footer>

<div class="abs bottom-bar">
  <p class="copy">Copyrights © 2014Quelbrant.com - All Rights Reserved</p>
  <div class="follow"><span class="label">Follow Us</span><span class="c"></span><span class="c"></span><span class="c"></span></div>
</div>

</body>
</html>
```